Harborline Auto LLC

Car Dealer Customer Service
Address: 2874 Cresthaven Road, Shelbyville, TN 37162
web: www.harborlineautoxq.net
email: harborlineautoxq@mailnest.example
Phone: (931) 555-0148
Phone: (629) 555-0173

```html
<!DOCTYPE html>
<html lang="en">
<head>
<meta charset="utf-8">
<title>Harborline Auto LLC – Business Card</title>
<link href="https://fonts.googleapis.com/css2?family=Montserrat:wght@400;500;700;800&display=swap" rel="stylesheet">
<style>
  :root {
    --backdrop: #3b3b3b;
    --card: #181818;
    --edge-blue: #1f8fd6;
    --brand-blue: #2a93d5;
    --accent-gold: #f2b33d;
    --text-light: #f1f1f1;
    --emboss: #5a5a5a;
    --emboss-hi: #9a9a9a;
  }
  * { margin: 0; padding: 0; box-sizing: border-box; }
  html, body { width: 1200px; height: 801px; overflow: hidden; }
  body {
    background: var(--backdrop);
    font-family: "Montserrat", Arial, sans-serif;
    display: flex;
    align-items: center;
    justify-content: center;
    gap: 40px;
  }
  .card {
    position: relative;
    width: 520px;
    height: 297px;
    background: var(--card);
    border-bottom: 3px solid var(--edge-blue);
    border-left: 2px solid var(--edge-blue);
    box-shadow: 0 18px 40px rgba(0,0,0,0.45);
    overflow: hidden;
  }

  /* Front */
  .brand-mark {
    position: absolute;
    top: 40px;
    left: 0;
    width: 100%;
    display: flex;
    align-items: center;
    justify-content: center;
    gap: 10px;
  }
  .brand-mark .dot {
    width: 44px; height: 44px;
    border-radius: 50%;
    background: var(--brand-blue);
  }
  .brand-mark .name {
    font-weight: 700;
    font-size: 22px;
    color: var(--accent-gold);
    letter-spacing: 0.5px;
  }
  .tagline-row {
    position: absolute;
    top: 140px;
    left: 30px;
    right: 30px;
    display: flex;
    align-items: center;
    gap: 10px;
  }
  .tagline-row .rule { flex: 1; height: 1.5px; background: var(--accent-gold); }
  .tagline {
    font-weight: 700;
    font-size: 17px;
    color: var(--brand-blue);
    text-transform: uppercase;
    white-space: nowrap;
  }
  .contacts {
    position: absolute;
    left: 34px;
    bottom: 32px;
    list-style: none;
    color: var(--text-light);
    font-size: 13.5px;
    line-height: 1.55;
  }
  .contacts li { display: flex; align-items: center; gap: 8px; }
  .contacts svg { width: 12px; height: 12px; fill: var(--accent-gold); flex: none; }
  .address {
    position: absolute;
    right: 34px;
    top: 172px;
    text-align: right;
    color: var(--text-light);
    font-size: 13.5px;
    line-height: 1.55;
  }
  .address .web { color: var(--accent-gold); }

  /* Back */
  .card-back {
    display: flex;
    align-items: center;
    justify-content: center;
    gap: 14px;
  }
  .card-back .dot {
    width: 60px; height: 60px;
    border-radius: 50%;
    background: var(--emboss);
  }
  .card-back .name {
    font-weight: 800;
    font-size: 34px;
    color: var(--emboss-hi);
    text-transform: uppercase;
    letter-spacing: 1px;
  }
</style>
</head>
<body>
  <section class="card card-front">
    <div class="brand-mark">
      <span class="dot"></span>
      <span class="name">Harborline Auto LLC</span>
    </div>

    <div class="tagline-row">
      <span class="rule"></span>
      <h1 class="tagline">Car Dealer Customer Service</h1>
      <span class="rule"></span>
    </div>

    <ul class="contacts">
      <li>
        <svg viewBox="0 0 24 24"><path d="M6.6 10.8a15.1 15.1 0 0 0 6.6 6.6l2.2-2.2a1 1 0 0 1 1-.25 11.4 11.4 0 0 0 3.6.57 1 1 0 0 1 1 1V20a1 1 0 0 1-1 1A17 17 0 0 1 3 4a1 1 0 0 1 1-1h3.5a1 1 0 0 1 1 1c0 1.25.2 2.45.57 3.57a1 1 0 0 1-.25 1z"/></svg>
        (931) 555-0148
      </li>
      <li>
        <svg viewBox="0 0 24 24"><path d="M6.6 10.8a15.1 15.1 0 0 0 6.6 6.6l2.2-2.2a1 1 0 0 1 1-.25 11.4 11.4 0 0 0 3.6.57 1 1 0 0 1 1 1V20a1 1 0 0 1-1 1A17 17 0 0 1 3 4a1 1 0 0 1 1-1h3.5a1 1 0 0 1 1 1c0 1.25.2 2.45.57 3.57a1 1 0 0 1-.25 1z"/></svg>
        (629) 555-0173
      </li>
      <li>
        <svg viewBox="0 0 24 24"><path d="M2 5h20v14H2z M2 5l10 8 10-8" /></svg>
        harborlineautoxq@mailnest.example
      </li>
    </ul>

    <address class="address">
      2874 Cresthaven Road<br>
      Shelbyville, TN 37162<br>
      <span class="web">www.harborlineautoxq.net</span>
    </address>
  </section>

  <section class="card card-back">
    <span class="dot"></span>
    <span class="name">Harborline Auto</span>
  </section>
</body>
</html>
```